Marlow Vale Stud website

We would like to create a horse stud/agistment farm website similar to this websites we have attached below:
www.thornbeck.com.au
www.quillstead.com.au
www.brackley.com
www.pimsey.com.au
The main colour scheme are purple and white to align with the stable's racing colours.
We have also attach the company logo and also images of the farm and create some ideas for the website.
Many thanks for looking into this project!

```html
<!DOCTYPE html>
<html lang="en">
<head>
<meta charset="utf-8">
<title>Marlow Vale Stud</title>
<link href="https://fonts.googleapis.com/css2?family=Montserrat:wght@400;600;700&family=Open+Sans:wght@400;600&display=swap" rel="stylesheet">
<style>
:root{
  --purple:#3d1a4d;
  --purple-dark:#2a0f36;
  --purple-mid:#5a2a6e;
  --ink:#222;
  --body:#555;
  --grey-band:#ebebeb;
  --ghost:#d9d9d9;
  --white:#fff;
}
*{box-sizing:border-box;margin:0;padding:0}
html,body{width:1200px;height:4532px;overflow:hidden;background:var(--white)}
body{position:relative;font-family:"Open Sans",Arial,sans-serif;color:var(--body)}
.abs{position:absolute}
.heading{font-family:"Montserrat",Arial,sans-serif;font-weight:700;color:var(--ink);letter-spacing:1px}
.ghost{position:absolute;left:0;width:1200px;text-align:center;font-family:"Montserrat",Arial,sans-serif;font-weight:700;font-size:76px;color:var(--ghost);letter-spacing:3px;opacity:.75}
.section-title{position:absolute;left:0;width:1200px;text-align:center;font-size:34px}
.lead{position:absolute;left:200px;width:800px;text-align:center;font-size:15px;line-height:26px}

/* header + hero */
.hero{position:absolute;left:0;top:0;width:1200px;height:790px;background:linear-gradient(180deg,#6f7a62 0%,#8a8463 35%,#b98a6d 60%,#5c7f3e 85%,#3f6a2a 100%)}
.hero-flowers{position:absolute;left:0;top:470px;width:1200px;height:150px;background:linear-gradient(90deg,#c9456f,#e6a13a,#d9527c,#f0c04c,#c94a6e)}
.topbar{position:absolute;left:0;top:0;width:1200px;height:150px;background:rgba(42,15,54,.92)}
.brand{position:absolute;left:100px;top:22px;display:flex;align-items:center;gap:16px;color:var(--white);font-family:"Montserrat",Arial,sans-serif;font-weight:600;font-size:38px}
.brand-dot{width:72px;height:72px;border-radius:50%;border:4px solid var(--white)}
.contact-chip{position:absolute;top:28px;display:flex;gap:14px;align-items:center;color:var(--white);font-size:15px;line-height:20px}
.contact-chip b{font-family:"Montserrat",Arial,sans-serif;font-weight:600;font-size:16px}
.nav{position:absolute;top:110px;right:90px;display:flex;gap:34px;font-family:"Montserrat",Arial,sans-serif;font-weight:600;font-size:15px;color:var(--white)}
.hero-name{position:absolute;left:760px;top:240px;width:300px;text-align:center;color:var(--white);font-family:"Montserrat",Arial,sans-serif;font-weight:600;font-size:38px}
.hero-name .dot{display:block;margin:0 auto 18px;width:90px;height:90px;border-radius:50%;border:5px solid var(--white)}

/* company */
.company-photo{position:absolute;left:96px;top:856px;width:392px;height:392px;border-radius:50%;border:10px solid var(--purple);background:linear-gradient(180deg,#5b88c9 0%,#8fb2de 40%,#7c6a55 65%,#5f7f3c 100%)}
.company-text{position:absolute;left:512px;top:920px;width:620px}
.company-text h2{font-size:30px;margin-bottom:18px}
.company-text p{font-size:15px;line-height:26px}
.btn{display:inline-flex;align-items:center;gap:10px;background:var(--purple);color:var(--white);font-family:"Montserrat",Arial,sans-serif;font-weight:600;font-size:14px;padding:13px 28px;border-radius:6px;border:none}

/* videos */
.band{position:absolute;left:0;width:1200px;background:var(--grey-band)}
.video-frame{position:absolute;left:220px;top:1540px;width:760px;height:380px;background:linear-gradient(180deg,#8996a3 0%,#c9b38e 35%,#4d5a3a 60%,#5d8a35 100%)}

/* stallions */
.stallion{position:absolute;width:302px;height:200px;background:linear-gradient(180deg,#86a6c8 0%,#9aa97a 55%,#4f7a35 100%)}
.stallion .label{position:absolute;left:0;bottom:0;width:100%;height:38px;background:var(--purple);color:var(--white);font-family:"Montserrat",Arial,sans-serif;font-weight:600;font-size:14px;line-height:38px;padding-left:36px}

/* news */
.news-card{position:absolute;top:2772px;width:330px}
.news-img{height:200px;background:linear-gradient(180deg,#9fb7d0 0%,#7c8a5c 50%,#4f7030 100%);position:relative}
.news-date{position:absolute;left:0;bottom:0;background:var(--purple);color:var(--white);font-size:12px;padding:6px 12px}
.news-card h3{font-size:17px;margin:26px 0 10px}
.news-card p{font-size:13px;line-height:22px}
.news-card .more{display:block;margin-top:12px;font-family:"Montserrat",Arial,sans-serif;font-weight:700;font-size:13px;color:var(--ink)}

/* contact info */
.info{position:absolute;top:3396px;width:300px;text-align:center;font-size:16px;line-height:24px;color:var(--ink)}
.info .icon{width:84px;height:84px;border-radius:50%;background:var(--purple);margin:0 auto 18px;display:flex;align-items:center;justify-content:center}

/* form */
.field{position:absolute;height:46px;border:1px solid #ddd;border-bottom:2px solid #c9c9c9;font-size:13px;color:#888;padding:14px 16px}
.field-tall{height:166px}
.submit{position:absolute;left:510px;top:3896px;width:180px;height:56px;justify-content:center;font-size:16px}

/* footer */
.footer{position:absolute;left:0;top:4020px;width:1200px;height:512px;background:linear-gradient(180deg,#3a1a47 0%,#2b1236 50%,#22102b 100%)}
.footer-inner{position:absolute;left:0;width:1200px;text-align:center;color:var(--white)}
.footer-name{top:210px;font-family:"Montserrat",Arial,sans-serif;font-weight:600;font-size:42px}
.footer-dot{position:absolute;left:560px;top:120px;width:80px;height:80px;border-radius:50%;border:5px solid var(--white)}
.footer-nav{font-family:"Montserrat",Arial,sans-serif;font-weight:600;font-size:15px}
.social{position:absolute;top:4354px;left:534px;display:flex;gap:12px}
.social span{width:26px;height:26px;border-radius:50%;border:2px solid var(--white);display:block}
</style>
</head>
<body>

<!-- hero -->
<section class="hero" role="img" aria-label="Jockey in purple silks riding a grey racehorse along a racecourse with flower beds"></section>
<div class="hero-flowers abs" role="img" aria-label="Racecourse flower beds"></div>
<header class="topbar">
  <div class="brand"><span class="brand-dot"></span>Marlow Vale Stud</div>
  <div class="contact-chip" style="left:660px">
    <svg width="34" height="34" viewBox="0 0 24 24" fill="#fff"><path d="M6.6 10.8a15 15 0 0 0 6.6 6.6l2.2-2.2c.3-.3.7-.4 1-.2 1.1.4 2.3.6 3.6.6.6 0 1 .4 1 1V20c0 .6-.4 1-1 1A17 17 0 0 1 3 4c0-.6.4-1 1-1h3.5c.6 0 1 .4 1 1 0 1.3.2 2.5.6 3.6.1.3 0 .7-.2 1z"/></svg>
    <div><b>Call us</b><br>(02) 5550 1187</div>
  </div>
  <div class="contact-chip" style="left:850px">
    <svg width="38" height="30" viewBox="0 0 24 18" fill="#fff"><path d="M0 0h24v18H0z" fill="none"/><path d="M1 1h22v16H1z" fill="#fff"/><path d="M1 1l11 8 11-8" stroke="#2a0f36" stroke-width="1.6" fill="none"/></svg>
    <div><b>Mail us</b><br>contact@marlowvalestud.com</div>
  </div>
  <nav class="nav"><span>HOME</span><span>NEWS</span><span>STALLIONS</span><span>SALES</span><span>VIDEOS</span><span>GALLERY</span><span>ABOUT</span></nav>
</header>
<div class="hero-name"><span class="dot"></span>Marlow Vale Stud</div>
<svg class="abs" style="left:0;top:640px" width="1200" height="160" viewBox="0 0 1200 160">
  <path d="M0 70 Q600 170 1200 70 L1200 160 L0 160Z" fill="#fff"/>
  <path d="M0 70 Q600 170 1200 70" fill="none" stroke="var(--purple)" stroke-width="14"/>
  <path d="M560 108 L600 128 L640 108" fill="none" stroke="#fff" stroke-width="6"/>
  <circle cx="600" cy="128" r="16" fill="#fff" stroke="var(--purple)" stroke-width="4"/>
</svg>

<!-- company -->
<div class="ghost" style="top:880px;left:260px">ABOUT US</div>
<div class="company-photo" role="img" aria-label="Group of horses standing in a paddock under a blue sky"></div>
<div class="company-text">
  <h2 class="heading">COMPANY</h2>
  <p>Sed ut perspiciatis unde omnis iste natus error sit voluptatem accusantium doloremque laudantium, totam rem aperiam, eaque ipsa quae ab illo inventore veritatis et quasi architecto beatae vitae dicta sunt explicabo. Nemo enim ipsam voluptatem quia voluptas sit aspernatur aut odit aut fugit, sed quia consequuntur magni dolores eos qui ratione voluptatem sequi nesciunt.</p>
  <div style="margin-top:22px"><span class="btn"><svg width="16" height="12" viewBox="0 0 24 18"><path d="M1 1h22v16H1z" fill="#fff"/><path d="M1 1l11 8 11-8" stroke="#3d1a4d" stroke-width="2" fill="none"/></svg>CONTACT US</span></div>
</div>

<!-- videos -->
<div class="band" style="top:1320px;height:400px"></div>
<div class="ghost" style="top:1370px">VIDEOS</div>
<h2 class="heading section-title" style="top:1394px">VIDEOS</h2>
<p class="lead" style="top:1452px">Sed ut perspiciatis unde omnis iste natus error sit voluptatem accusantium doloremque laudantium, totam rem aperiam, eaque ipsa quae ab illo inventore veritatis et quasi architecto beatae vitae dicta sunt explicabo.</p>
<div class="video-frame" role="img" aria-label="Video still of horses grazing on a hillside at sunset"></div>
<svg class="abs" style="left:566px;top:1696px" width="68" height="68" viewBox="0 0 68 68"><circle cx="34" cy="34" r="30" fill="none" stroke="#fff" stroke-width="3" opacity=".85"/><path d="M27 22 L48 34 L27 46Z" fill="#fff" opacity=".85"/></svg>

<!-- stallions -->
<div class="ghost" style="top:1966px">STALLIONS</div>
<h2 class="heading section-title" style="top:1992px">STALLIONS</h2>
<p class="lead" style="top:2050px">Sed ut perspiciatis unde omnis iste natus error sit voluptatem accusantium doloremque laudantium, totam rem aperiam, eaque ipsa quae ab illo inventore veritatis et quasi architecto beatae vitae dicta sunt explicabo.</p>
<div class="stallion" style="left:112px;top:2150px" role="img" aria-label="Chestnut stallion standing in a field"><div class="label">Sed ut perspiciatis</div></div>
<div class="stallion" style="left:448px;top:2150px" role="img" aria-label="Bay stallion standing in a paddock"><div class="label">Sed ut perspiciatis</div></div>
<div class="stallion" style="left:784px;top:2150px" role="img" aria-label="Chestnut stallion by a fence"><div class="label">Sed ut perspiciatis</div></div>
<div class="stallion" style="left:112px;top:2376px" role="img" aria-label="Red chestnut stallion on grass"><div class="label">Sed ut perspiciatis</div></div>
<div class="stallion" style="left:448px;top:2376px" role="img" aria-label="Palomino stallion under trees"><div class="label">Sed ut perspiciatis</div></div>
<div class="stallion" style="left:784px;top:2376px" role="img" aria-label="Dark bay stallion by a stable"><div class="label">Sed ut perspiciatis</div></div>

<!-- news -->
<div class="band" style="top:2636px;height:560px"></div>
<div class="ghost" style="top:2680px">OUR NEWS</div>
<h2 class="heading section-title" style="top:2702px">OUR NEWS</h2>
<article class="news-card" style="left:96px">
  <div class="news-img" role="img" aria-label="Aerial view of stud farm buildings and paddocks"><span class="news-date">Oct 27 2016</span></div>
  <h3 class="heading">SED UT PERSPICIATIS UND</h3>
  <p>Sed ut perspiciatis unde omnis iste natus error sit voluptatem accusantium doloremque laudantium, totam rem aperiam, eaque ipsa quae ab illo.</p>
  <span class="more">READ MORE</span>
</article>
<article class="news-card" style="left:434px">
  <div class="news-img" role="img" aria-label="Farm homestead surrounded by green pastures"><span class="news-date">Oct 27 2016</span></div>
  <h3 class="heading">SED UT PERSPICIATIS UND</h3>
  <p>Sed ut perspiciatis unde omnis iste natus error sit voluptatem accusantium doloremque laudantium, totam rem aperiam, eaque ipsa quae ab illo.</p>
  <span class="more">READ MORE</span>
</article>
<article class="news-card" style="left:772px">
  <div class="news-img" role="img" aria-label="Stable yard with horses and trees"><span class="news-date">Oct 27 2016</span></div>
  <h3 class="heading">SED UT PERSPICIATIS UND</h3>
  <p>Sed ut perspiciatis unde omnis iste natus error sit voluptatem accusantium doloremque laudantium, totam rem aperiam, eaque ipsa quae ab illo.</p>
  <span class="more">READ MORE</span>
</article>

<!-- contact information -->
<div class="ghost" style="top:3246px">CONTACT INFORMATION</div>
<h2 class="heading section-title" style="top:3272px;font-size:32px">CONTACT INFORMATION</h2>
<p class="abs" style="top:3324px;left:0;width:1200px;text-align:center;font-size:17px;color:var(--ink)">Contact us for more information</p>
<div class="info" style="left:160px">
  <div class="icon"><svg width="30" height="40" viewBox="0 0 24 32"><path d="M12 0C5.4 0 0 5.4 0 12c0 9 12 20 12 20s12-11 12-20C24 5.4 18.6 0 12 0z" fill="#fff"/><circle cx="12" cy="12" r="4.5" fill="#3d1a4d"/></svg></div>
  48 Linden Ridge Rd<br>Harlow Creek, NSW 2337
</div>
<div class="info" style="left:450px">
  <div class="icon"><svg width="36" height="36" viewBox="0 0 24 24" fill="#fff"><path d="M6.6 10.8a15 15 0 0 0 6.6 6.6l2.2-2.2c.3-.3.7-.4 1-.2 1.1.4 2.3.6 3.6.6.6 0 1 .4 1 1V20c0 .6-.4 1-1 1A17 17 0 0 1 3 4c0-.6.4-1 1-1h3.5c.6 0 1 .4 1 1 0 1.3.2 2.5.6 3.6.1.3 0 .7-.2 1z"/></svg></div>
  Phone:<br>555 014 2290
</div>
<div class="info" style="left:760px">
  <div class="icon"><svg width="38" height="28" viewBox="0 0 24 18"><path d="M1 1h22v16H1z" fill="#fff"/><path d="M1 1l11 8 11-8" stroke="#3d1a4d" stroke-width="1.6" fill="none"/></svg></div>
  Email:<br>info@marlowvalestud.com
</div>

<!-- contact form -->
<div class="ghost" style="top:3580px">CONTACT US</div>
<h2 class="heading section-title" style="top:3604px;font-size:32px">CONTACT US</h2>
<div class="field" style="left:160px;top:3680px;width:430px">First Name</div>
<div class="field" style="left:610px;top:3680px;width:430px">Last Name</div>
<div class="field" style="left:160px;top:3740px;width:430px">Company</div>
<div class="field field-tall" style="left:610px;top:3740px;width:430px">Message</div>
<div class="field" style="left:160px;top:3800px;width:430px">Email Address</div>
<div class="field" style="left:160px;top:3860px;width:430px">Phone Number</div>
<span class="btn submit"><svg width="16" height="16" viewBox="0 0 24 24"><path d="M2 12L22 2 16 22 12 14Z" fill="#fff"/></svg>Submit</span>

<!-- footer -->
<footer class="footer" role="img" aria-label="Dusk view over the farm paddocks tinted purple"></footer>
<svg class="abs" style="left:0;top:4000px" width="1200" height="90" viewBox="0 0 1200 90">
  <path d="M0 0 H1200 V20 Q600 110 0 20Z" fill="#fff"/>
  <path d="M0 20 Q600 110 1200 20" fill="none" stroke="#5a2a6e" stroke-width="6"/>
</svg>
<span class="footer-dot" style="top:4140px"></span>
<div class="footer-inner footer-name" style="top:4228px">Marlow Vale Stud</div>
<div class="footer-inner footer-nav" style="top:4304px">Home &nbsp;|&nbsp; News &nbsp;|&nbsp; Stallions &nbsp;|&nbsp; Sales &nbsp;|&nbsp; Videos &nbsp;|&nbsp; Gallery &nbsp;|&nbsp; About</div>
<div class="social"><span></span><span></span><span></span><span></span></div>
<div class="footer-inner footer-nav" style="top:4404px">Privacy Policy &nbsp;|&nbsp; Contact us &nbsp;|&nbsp; Terms of Service</div>
<div class="footer-inner" style="top:4452px;font-size:13px;opacity:.8">© 2016 Marlow Vale Stud. All rights reserved.</div>

</body>
</html>
```